Consulting company business cards

We have a base design, but would be willing to update. We have a new logo/"tag" that needs to be added. Current business card design is attached for reference into our "style."

Industry/Entity Type

Business

Contact Information for Business Card

Should contain name and title, office number, mobile number if appropriate, e-mail, website, physical address, and company logo.

Font styles to use
Other font styles liked:
• See current card design on KorvandBCard

Colors
0455a3
85acd3
aaaaaa

Requirements
Must have
• Our colors are navy blue, gray, and a lighter blue
Nice to have
• Design that I can easily drop in new names/titles as we hire employees.

```html
<!DOCTYPE html>
<html lang="en">
<head>
<meta charset="utf-8">
<title>Tavrin Business Cards</title>
<link rel="stylesheet" href="https://fonts.googleapis.com/css2?family=Source+Sans+3:wght@400;600;700&display=swap">
<style>
  :root {
    --navy: #06304f;
    --navy-deep: #032a47;
    --light-blue: #86aed3;
    --paper: #ffffff;
    --ink: #1c1c1c;
    --backdrop: #151515;
    --web-text: #d3dde8;
  }
  * { margin: 0; padding: 0; box-sizing: border-box; }
  html, body {
    width: 1200px;
    height: 900px;
    overflow: hidden;
    background: var(--backdrop);
    font-family: "Source Sans 3", sans-serif;
  }
  .stage { position: relative; width: 1200px; height: 900px; }
  .card {
    position: absolute;
    top: 170px;
    width: 347px;
    height: 561px;
    overflow: hidden;
    text-align: center;
  }
  .card--front { left: 259px; background: var(--paper); color: var(--ink); }
  .card--back { left: 631px; background: var(--navy-deep); color: var(--paper); }

  .accent-band {
    position: absolute;
    left: 102px;
    width: 143px;
    background: var(--navy);
  }
  .accent-band--top { top: 0; height: 30px; }
  .accent-band--bottom { bottom: 0; height: 28px; }

  .brand {
    position: absolute;
    left: 0;
    width: 100%;
  }
  .brand__row {
    display: flex;
    justify-content: center;
    align-items: center;
    gap: 8px;
  }
  .brand__name {
    font-weight: 700;
    font-size: 54px;
    line-height: 1;
    letter-spacing: 2px;
  }
  .brand__dot {
    width: 40px;
    height: 40px;
    border-radius: 50%;
  }
  .brand__tagline {
    margin-top: 6px;
    font-size: 12.5px;
    letter-spacing: 2px;
    font-weight: 400;
  }
  .card--front .brand { top: 305px; top: 135px; }
  .card--front .brand__name { color: var(--navy); }
  .card--front .brand__dot { background: var(--light-blue); }
  .card--front .brand__tagline { color: var(--navy); }

  .card--back .brand { top: 243px; }
  .card--back .brand__name { color: var(--paper); }
  .card--back .brand__dot { background: var(--paper); }
  .card--back .brand__tagline { color: var(--paper); }

  .contact {
    position: absolute;
    top: 306px;
    left: 0;
    width: 100%;
    font-size: 15.5px;
    line-height: 20px;
  }
  .contact__name {
    font-size: 20px;
    font-weight: 600;
    color: var(--navy);
    line-height: 26px;
  }
  .contact__title { margin-bottom: 18px; }
  .contact__group { margin-bottom: 22px; }

  .brand-mark-area {
    position: absolute;
    left: 105px;
    top: 280px;
    width: 242px;
    height: 281px;
    background: radial-gradient(ellipse at 60% 40%, rgba(40, 90, 130, 0.55), rgba(40, 90, 130, 0) 70%);
  }
  .website {
    position: absolute;
    top: 441px;
    left: 0;
    width: 100%;
    font-size: 15.5px;
    color: var(--web-text);
  }
</style>
</head>
<body>
<main class="stage">
  <section class="card card--front" aria-label="Business card front">
    <div class="accent-band accent-band--top"></div>
    <div class="brand">
      <div class="brand__row">
        <span class="brand__name">TAVRIN</span>
        <span class="brand__dot"></span>
      </div>
      <p class="brand__tagline">A CLOUD CONSULTING COMPANY</p>
    </div>
    <div class="contact">
      <p class="contact__name">Marissa Korvand</p>
      <p class="contact__title">Managing Director</p>
      <div class="contact__group">
        <p>317.555.0148</p>
        <p>317.555.0162</p>
        <p>mkorvand@tavrintech.com</p>
      </div>
      <p>3185 W 61 st indianapolis</p>
      <p>indiana 46260</p>
    </div>
    <div class="accent-band accent-band--bottom"></div>
  </section>

  <section class="card card--back" aria-label="Business card back">
    <div class="brand-mark-area" role="img" aria-label="Faint large brand decoration"></div>
    <div class="brand">
      <div class="brand__row">
        <span class="brand__name">TAVRIN</span>
        <span class="brand__dot"></span>
      </div>
      <p class="brand__tagline">A CLOUD CONSULTING COMPANY</p>
    </div>
    <p class="website">www.tavrintech.com</p>
  </section>
</main>
</body>
</html>
```